Compnay PowerPoint Tempalte Design

I am needing a good base design and slide designs for interior and exterior company presentations. The template will need to be on the company brand with proper coloring and fonts. Able to be creative with layout options with a good example attached.
website for reference: www.crewvlt.com/

Target Market(s)

Professionals

Font styles to use
Other font styles liked:
• Helvetica

Requirements
Must have
• On Brand Colors, Clean, simple design

```html
<!DOCTYPE html>
<html lang="en">
<head>
<meta charset="utf-8">
<title>VLT Presentation Template</title>
<link href="https://fonts.googleapis.com/css2?family=Roboto:wght@400;500;700;900&display=swap" rel="stylesheet">
<style>
:root{
  --teal:#4a9d90;
  --blue:#0e79a2;
  --forest:#1d5a52;
  --ink:#231f20;
  --copy:#6a6a6a;
  --page:#c4c4c4;
  --white:#ffffff;
}
*{margin:0;padding:0;box-sizing:border-box}
html,body{width:1200px;height:3376px;overflow:hidden}
body{background:var(--page);font-family:"Roboto",Helvetica,Arial,sans-serif;color:var(--ink);position:relative}
.slide{position:absolute;left:109px;width:982px;height:551px;background:var(--white);overflow:hidden}
.brand{position:absolute;display:flex;align-items:center;gap:6px;font-weight:900;color:var(--ink);letter-spacing:1px}
.brand .dot{width:12px;height:12px;background:var(--teal)}
.slide-head .brand{left:861px;top:44px;font-size:26px}
.marker{position:absolute;left:0;top:37px;width:35px;height:40px}
.slide-title{position:absolute;left:59px;top:36px;font-size:37px;font-weight:900;letter-spacing:.5px;line-height:44px}
.footer{position:absolute;left:0;bottom:0;width:100%;height:24px}
.footer svg{position:absolute;inset:0}
.footer p{position:absolute;left:61px;top:5px;font-size:10.5px;color:var(--white)}
.photo{position:absolute}

/* cover */
.cover .brand{left:59px;top:58px;font-size:22px}
.cover-title{position:absolute;left:57px;top:214px;font-size:54px;font-weight:900;letter-spacing:1px}
.cover-tag{position:absolute;left:59px;top:300px;width:338px;font-size:12.5px;font-weight:700;line-height:22px}
.cover-art{position:absolute;left:389px;top:0;width:593px;height:551px;background:linear-gradient(100deg,#fff 0%,#fff 22%,#5ea89b 22.2%,#2f7d73 55%,#0e79a2 100%)}

/* about */
.about-frame{position:absolute;left:49px;top:131px;width:305px;height:222px;background:var(--teal)}
.about-photo{left:60px;top:141px;width:396px;height:326px;background:linear-gradient(135deg,#3a2c22,#8a6a4d 55%,#d7c3a8)}
.about-copy{position:absolute;left:507px;top:154px;width:415px;font-size:15px;line-height:27.5px;color:var(--copy);text-align:justify}
.about-copy p+p{margin-top:21px}

/* services */
.service{position:absolute;top:172px;width:262px;height:236px;background:var(--white);border-radius:6px;box-shadow:0 3px 10px rgba(0,0,0,.18)}
.service .photo{left:4px;top:4px;width:254px;height:176px;border-radius:5px 5px 0 0}
.service .badge{position:absolute;left:107px;top:156px;width:48px;height:48px;border-radius:50%;background:var(--teal);border:3px solid var(--white);display:flex;align-items:center;justify-content:center}
.service h3{position:absolute;left:0;right:0;top:212px;text-align:center;font-size:12.5px;font-weight:700}

/* values */
.hub{position:absolute;left:360px;top:165px;width:262px;height:262px;border-radius:50%;background:#f4f4f4;box-shadow:0 0 8px rgba(0,0,0,.08)}
.hub-inner{position:absolute;left:17px;top:17px;width:228px;height:228px;border-radius:50%;background:var(--white);box-shadow:0 2px 10px rgba(0,0,0,.12);display:flex;align-items:center;justify-content:center;gap:10px;font-size:56px;font-weight:900;letter-spacing:2px}
.hub-inner .dot{width:22px;height:22px;background:var(--teal)}
.value{position:absolute;width:235px}
.value h4{font-size:13px;font-weight:700;margin-bottom:10px}
.value p{font-size:11.5px;line-height:20px;color:var(--copy)}
.value.left{text-align:right}
.icon-dot{position:absolute;width:56px;height:56px;border-radius:50%;display:flex;align-items:center;justify-content:center}

/* team */
.member{position:absolute;top:159px;width:269px;height:308px;background:var(--white);box-shadow:0 2px 10px rgba(0,0,0,.15);text-align:center}
.avatar{position:absolute;left:95px;top:-39px;width:78px;height:78px;border-radius:50%;border:3px solid var(--blue);background:linear-gradient(160deg,#cfd6dc,#7f8a93)}
.member h5{margin-top:64px;font-size:12px;font-weight:700}
.member .role{font-size:9.5px;margin-top:2px}
.member .bio{padding:0 18px;margin-top:14px;font-size:10.5px;line-height:19px;color:var(--copy)}
.member .bio p+p{margin-top:8px}
</style>
</head>
<body>

<!-- Cover -->
<section class="slide cover" style="top:166px">
  <div class="brand"><span class="dot"></span>VLT</div>
  <h1 class="cover-title">VLT</h1>
  <p class="cover-tag">Where we maintain a passion for excellence, striving to be better each and every day, so that our guests leave happy and our team members feel fulfilled.</p>
  <div class="cover-art" role="img" aria-label="Team photo of smiling colleagues with teal and blue colour overlay"></div>
</section>

<!-- About -->
<section class="slide slide-head" style="top:789px">
  <svg class="marker" viewBox="0 0 35 40"><polygon points="0,0 35,20 0,40" fill="var(--forest)"/></svg>
  <h2 class="slide-title">ABOUT US</h2>
  <div class="brand"><span class="dot"></span>VLT</div>
  <div class="about-frame"></div>
  <div class="photo about-photo" role="img" aria-label="Photo of a group of women laughing together over coffee at a café table"></div>
  <div class="about-copy">
    <p>VLT is dedicated to cultivating a positive culture of leadership for its team members’ professional and personal development, and this person-focused mentality transfers throughout the company from partners to our teams to guests.</p>
    <p>We strive to ensure each team member feels valued in all aspects of their role, reinforcing the importance of fostering a self-sustaining culture of success where everyone makes a team effort to communicate and overcome adversity.</p>
  </div>
  <div class="footer">
    <svg viewBox="0 0 982 24" preserveAspectRatio="none"><rect width="982" height="24" fill="var(--teal)"/><polygon points="0,0 428,0 414,24 0,24" fill="var(--blue)"/></svg>
    <p>©Copyright ©2021 . Company Name . All Rights Reserve</p>
  </div>
</section>

<!-- Services -->
<section class="slide slide-head" style="top:1411px">
  <svg class="marker" viewBox="0 0 35 40"><polygon points="0,0 35,20 0,40" fill="var(--forest)"/></svg>
  <h2 class="slide-title">WHAT WE DO</h2>
  <div class="brand"><span class="dot"></span>VLT</div>
  <article class="service" style="left:68px">
    <div class="photo" role="img" aria-label="Photo of a restaurant counter and open kitchen with shelves" style="background:linear-gradient(180deg,#d9d4cc 0%,#bdb2a3 45%,#5a5550 60%,#b2692c 100%)"></div>
    <div class="badge"><svg width="22" height="22" viewBox="0 0 22 22" fill="none" stroke="#fff" stroke-width="1.6"><path d="M2 8h18l-2-5H4z"/><path d="M4 8v11h14V8"/><rect x="9" y="13" width="4" height="6"/></svg></div>
    <h3>RESTAURANTS</h3>
  </article>
  <article class="service" style="left:364px">
    <div class="photo" role="img" aria-label="Photo of a hand holding a house key over a desk" style="background:linear-gradient(135deg,#a67c52,#d8c3a5 50%,#8f7358)"></div>
    <div class="badge"><svg width="22" height="22" viewBox="0 0 22 22" fill="none" stroke="#fff" stroke-width="1.6"><path d="M3 11l8-7 8 7"/><path d="M5 9v10h12V9"/><rect x="9" y="13" width="4" height="6"/></svg></div>
    <h3>REAL ESTATE</h3>
  </article>
  <article class="service" style="left:660px">
    <div class="photo" role="img" aria-label="Photo of people signing documents at a table" style="background:linear-gradient(135deg,#9fb58f,#e4e6ea 45%,#c8ccd2 75%,#6b3a2a)"></div>
    <div class="badge"><svg width="22" height="22" viewBox="0 0 22 22" fill="none" stroke="#fff" stroke-width="1.6"><path d="M4 18l2-5 9-9 3 3-9 9z"/><path d="M3 20h16"/></svg></div>
    <h3>DEVELOPMENT</h3>
  </article>
  <div class="footer">
    <svg viewBox="0 0 982 24" preserveAspectRatio="none"><rect width="982" height="24" fill="var(--teal)"/><polygon points="0,0 428,0 414,24 0,24" fill="var(--blue)"/></svg>
    <p>©Copyright ©2021 . Company Name . All Rights Reserve</p>
  </div>
</section>

<!-- Values -->
<section class="slide slide-head" style="top:2033px">
  <svg class="marker" viewBox="0 0 35 40"><polygon points="0,0 35,20 0,40" fill="var(--forest)"/></svg>
  <h2 class="slide-title">OUR CORE VALUES</h2>
  <div class="brand"><span class="dot"></span>VLT</div>

  <div class="hub"><div class="hub-inner"><span class="dot"></span>VLT</div></div>

  <div class="value left" style="left:39px;top:191px"><h4>INTEGRITY</h4><p>Integrity in everything we do. Do the right thing, even when no one is looking.</p></div>
  <div class="icon-dot" style="left:294px;top:193px;background:var(--teal)"><svg width="26" height="26" viewBox="0 0 26 26" fill="none" stroke="#fff" stroke-width="1.6"><rect x="4" y="4" width="18" height="18" rx="2"/><path d="M8 13l4 4 7-8"/></svg></div>

  <div class="value left" style="left:39px;top:334px"><h4>FAMILY</h4><p>Family first, always. All decisions must benefit our family and the company.</p></div>
  <div class="icon-dot" style="left:294px;top:336px;background:var(--blue)"><svg width="26" height="26" viewBox="0 0 26 26" fill="none" stroke="#fff" stroke-width="1.6"><circle cx="9" cy="8" r="3"/><circle cx="17" cy="8" r="3"/><path d="M3 21c0-5 3-8 6-8s6 3 6 8"/><path d="M13 21c0-5 2-8 4-8s6 3 6 8"/></svg></div>

  <div class="icon-dot" style="left:634px;top:193px;background:var(--forest)"><svg width="26" height="26" viewBox="0 0 26 26" fill="none" stroke="#fff" stroke-width="1.6"><path d="M3 13l5-5 5 4 5-4 5 5-10 8z"/></svg></div>
  <div class="value" style="left:710px;top:191px"><h4>ESPECT</h4><p>We care for one another, praise efforts, recognize progress, and reward results.</p></div>

  <div class="icon-dot" style="left:634px;top:336px;background:var(--teal)"><svg width="26" height="26" viewBox="0 0 26 26" fill="none" stroke="#fff" stroke-width="1.6"><path d="M13 22s-9-5-9-12a5 5 0 0 1 9-2 5 5 0 0 1 9 2c0 7-9 12-9 12z"/></svg></div>
  <div class="value" style="left:710px;top:334px"><h4>PASSION</h4><p>We are positive, hardworking, and disciplined in all we do, which stems</p></div>

  <div class="footer">
    <svg viewBox="0 0 982 24" preserveAspectRatio="none"><rect width="982" height="24" fill="var(--teal)"/><polygon points="0,0 428,0 414,24 0,24" fill="var(--blue)"/></svg>
    <p>©Copyright ©2021 . Company Name . All Rights Reserve</p>
  </div>
</section>

<!-- Team -->
<section class="slide slide-head" style="top:2655px">
  <svg class="marker" viewBox="0 0 35 40"><polygon points="0,0 35,20 0,40" fill="var(--forest)"/></svg>
  <h2 class="slide-title">MEET THE TEAM</h2>
  <div class="brand"><span class="dot"></span>VLT</div>

  <article class="member" style="left:62px">
    <div class="avatar" role="img" aria-label="Portrait photo of the CEO"></div>
    <h5>RYAN HOLLIS</h5><p class="role">CEO</p>
    <div class="bio">
      <p>Growing up in Wichita, Kansas, where Sammy’s started, Ryan has long felt a connection with the group that started the concept, enjoying the food, culture, and opportunity to be a part of this incredible brand.</p>
      <p>Ryan has owned and operated businesses since the young age of eight, starting as the neighborhood kid who mowed lawns which grew into a full-time job in high school.</p>
    </div>
  </article>

  <article class="member" style="left:359px">
    <div class="avatar" role="img" aria-label="Portrait photo of the controller"></div>
    <h5>DANA WHITFIELD,</h5><p class="role">CONTROLLER</p>
    <div class="bio">
      <p>Dana Whitfield is a brilliant veteran of the finance and accounting industries, utilizing her experience to elevate VLT and its team members and customers. With two years (and counting) under her belt with VLT.</p>
      <p>Dana has immediately connected with the family-feeling of this company and enjoys the ongoing learning process of working in a new industry, an industry that certainly</p>
    </div>
  </article>

  <article class="member" style="left:656px">
    <div class="avatar" role="img" aria-label="Portrait photo of the COO"></div>
    <h5>MARCUS BELL,</h5><p class="role">COO</p>
    <div class="bio">
      <p>Seizing opportunities to change peoples’ lives, in front of and behind the counter, Marcus Bell genuinely enjoys the people-aspect of the food and service industries.</p>
      <p>At 19 years old, an Area Director had told Marcus that he believed Marcus was born for this industry and should consider making it his passion.</p>
    </div>
  </article>

  <div class="footer">
    <svg viewBox="0 0 982 24" preserveAspectRatio="none"><rect width="982" height="24" fill="var(--teal)"/><polygon points="0,0 428,0 414,24 0,24" fill="var(--blue)"/></svg>
    <p>©Copyright ©2021 . Company Name . All Rights Reserve</p>
  </div>
</section>

</body>
</html>
```